Corvena Hotel, city center modern minimal hotel operating all year round, on Rhodes island Greece

city, modern ,all year operating hotel

Target Market(s)

tourists, business agents

Industry/Entity Type

tourism

Number of Pages Required

2 page

Requirements
Must have
• room type photos and descriptions, amenities individual listing (graphic), comments sections, map driving location details
Nice to have
• gallery section, modern and minimal design, amenities section, individual room type descriptions, photos and facilities

```html
<!DOCTYPE html>
<html lang="en">
<head>
<meta charset="utf-8">
<title>Corvena Hotel</title>
<link href="https://fonts.googleapis.com/css2?family=Marcellus&family=Jost:ital,wght@0,300;0,400;0,500;0,600;1,300;1,400&display=swap" rel="stylesheet">
<style>
:root{
  --green:#1e5235;
  --green-dark:#1a3a2c;
  --gold:#d3a33a;
  --ink:#222;
  --muted:#6a6a6a;
  --line:#e3e3e3;
  --footer:#2b2b2b;
  --white:#fff;
}
*{box-sizing:border-box;margin:0;padding:0}
html,body{width:1200px;height:4694px;overflow:hidden;background:var(--white)}
body{position:relative;font-family:"Jost",sans-serif;color:var(--ink)}
.abs{position:absolute}
.serif{font-family:"Marcellus",serif;font-weight:400}
.btn{position:absolute;display:flex;align-items:center;justify-content:center;gap:6px;background:var(--gold);color:var(--white);font:600 14px "Jost",sans-serif;letter-spacing:.5px;text-transform:uppercase}
.btn .dot{width:11px;height:11px;border-radius:50%;background:var(--white);display:inline-block}

.topbar{position:absolute;left:0;top:0;width:1200px;height:40px;border-bottom:1px solid var(--line)}
.topbar .social{position:absolute;left:98px;top:13px;display:flex;gap:12px}
.topbar .social span{width:13px;height:13px;border-radius:3px;background:var(--green)}
.topbar .contact{position:absolute;right:98px;top:10px;font-size:13px;color:var(--muted);display:flex;gap:18px;align-items:center}
.topbar .contact svg{vertical-align:-2px;margin-right:4px}

.header{position:absolute;left:0;top:40px;width:1200px;height:75px}
.brand{position:absolute;display:flex;align-items:center;gap:12px;color:var(--green);font-family:"Marcellus",serif;white-space:nowrap}
.brand .mark{background:var(--gold)}
.header .brand{left:100px;top:17px;font-size:32px}
.header .brand .mark{width:34px;height:34px}
.nav{position:absolute;right:270px;top:27px;display:flex;gap:28px;font-size:15px;color:var(--ink)}
.header .btn{left:956px;top:12px;width:146px;height:42px}

.hero{position:absolute;left:0;top:115px;width:1200px;height:505px;background:linear-gradient(100deg,#2c241d 0%,#5a4a3c 45%,#8c7a66 70%,#4b3f35 100%)}
.hero .eyebrow{left:100px;top:150px;color:var(--white);font-size:15px;letter-spacing:2px}
.hero h1{left:100px;top:175px;color:var(--white);font-size:58px;line-height:68px;letter-spacing:1px}
.hero .slides{left:1090px;top:166px;color:var(--white);font-size:15px}
.hero .slides .rule{position:absolute;left:4px;top:24px;width:1px;height:110px;background:rgba(255,255,255,.7)}
.booking label{position:absolute;top:413px;color:var(--white);font-size:14px;letter-spacing:2px}
.booking .field{position:absolute;top:437px;height:42px;background:var(--white);border:1px solid #ccc;color:#999;font-size:14px;padding:11px 14px;display:flex;justify-content:space-between}
.booking .btn{left:846px;top:437px;width:230px;height:42px}

.emblem{left:100px;top:700px;width:470px;height:355px;background:linear-gradient(135deg,#e4c373 0%,#d3a33a 45%,#2d7a52 55%,#1e5235 100%);opacity:.9}
.welcome .eyebrow{left:611px;top:727px;font-size:18px;letter-spacing:3px;color:#333}
.welcome h2{left:606px;top:756px;font-size:58px;color:#222;letter-spacing:1px;white-space:nowrap}
.welcome p{left:611px;top:832px;width:490px;font-size:14px;line-height:26px;color:var(--muted);font-weight:300}
.welcome .btn{left:611px;top:943px;width:150px;height:42px}

.section-eyebrow{width:1200px;text-align:center;font-size:18px;letter-spacing:3px;color:#333}
.section-title{width:1200px;text-align:center;color:#222}

.room{position:absolute;overflow:hidden}
.room .photo{position:absolute;inset:0}
.room .name{position:absolute;left:9px;bottom:38px;color:var(--white);font-family:"Marcellus",serif;font-size:27px}
.room .meta{position:absolute;left:11px;bottom:14px;color:var(--white);font-size:14px;display:flex;gap:16px}
.room .meta svg{vertical-align:-2px;margin-right:4px}

.amenities{position:absolute;left:0;top:1831px;width:1200px;height:237px;background:linear-gradient(90deg,#1b3a2b,#20432f 50%,#1a382a)}
.amenity{position:absolute;top:95px;display:flex;gap:14px;align-items:center;color:var(--white)}
.amenity .t{font-family:"Marcellus",serif;font-size:27px;line-height:30px}
.amenity .s{font-size:14px;letter-spacing:2px;color:#cfd8d2}

.services .eyebrow{left:98px;top:2193px;font-size:18px;letter-spacing:3px;color:#333}
.services h2{left:98px;top:2219px;font-size:58px;line-height:74px;color:#222}
.services p{left:98px;top:2384px;width:410px;font-size:14px;line-height:26.5px;color:var(--muted);font-weight:300}
.services .thumb{position:absolute;left:868px;width:88px;height:88px}
.services .lbl{position:absolute;left:970px}
.services .lbl small{display:block;font-size:13px;color:var(--green)}
.services .lbl b{display:block;font-family:"Marcellus",serif;font-weight:400;font-size:21px;color:var(--gold)}

.testimonial{position:absolute;left:0;top:2623px;width:1200px;height:534px;overflow:hidden}
.testimonial .photo{position:absolute;left:560px;top:0;width:640px;height:534px;background:linear-gradient(135deg,#c9b9a4,#eeeae3 45%,#f6f4ef 70%,#d9cfc1)}
.testimonial .panel{position:absolute;left:0;top:0;width:612px;height:534px;background:var(--green);border-bottom-right-radius:150px}
.testimonial .eyebrow{left:98px;top:95px;color:var(--white);font-size:18px;letter-spacing:2px}
.testimonial h2{left:100px;top:112px;color:var(--gold);font-size:58px}
.testimonial blockquote{position:absolute;left:104px;top:205px;width:450px;color:var(--white);font-style:italic;font-weight:300;font-size:23px;line-height:35px}
.testimonial .stars{left:98px;top:380px;display:flex;gap:4px}
.testimonial .who{left:98px;top:410px;color:var(--white);font-size:27px;font-weight:500}
.testimonial .arrows{left:432px;top:438px;display:flex;gap:10px}
.testimonial .arrows span{width:38px;height:38px;border-radius:50%;display:flex;align-items:center;justify-content:center}

.gallery .tile{position:absolute}

.contact-sec{position:absolute;left:0;top:3781px;width:1200px;height:542px;background:linear-gradient(110deg,#d9d2c7 0%,#efe9df 30%,#c98d55 48%,#e6dfd3 65%,#f2efe9 100%)}
.contact-card{position:absolute;left:700px;top:3819px;width:402px;height:471px;background:var(--green);border-radius:44px}
.contact-card h2{position:absolute;left:22px;top:50px;color:var(--gold);font-size:56px;white-space:nowrap}
.contact-card .input{position:absolute;left:22px;width:358px;border:1px solid #8fa89a;color:var(--white);font-size:15px;padding:8px 8px}
.contact-card .btn{left:22px;top:382px;width:146px;height:42px}

.footer{position:absolute;left:0;top:4323px;width:1200px;height:371px;background:var(--footer);color:#b9b9b9}
.footer .brand{left:100px;top:103px;font-size:32px;color:var(--green)}
.footer .brand .mark{width:36px;height:36px}
.footer .social{position:absolute;left:100px;top:204px;display:flex;gap:14px}
.footer .social span{width:44px;height:44px;border-radius:50%;background:var(--gold)}
.footer h4{position:absolute;top:67px;font-family:"Marcellus",serif;font-weight:400;color:var(--gold);font-size:22px}
.footer ul{position:absolute;list-style:none;font-size:14px;line-height:36px}
.footer ul li::before{content:"› ";color:var(--gold)}
.footer .info{position:absolute;left:589px;top:112px;font-size:14px;line-height:24px}
.footer .info div{margin-bottom:10px;display:flex;gap:8px}
.footer .nl{position:absolute;left:832px;top:112px;width:270px;font-size:14px;line-height:24px}
.footer .nl .email{margin-top:26px;border-bottom:1px solid #888;padding-bottom:6px;display:flex;justify-content:space-between}
.footer .rule{position:absolute;left:100px;top:316px;width:1002px;height:1px;background:#4a4a4a}
.footer .copy{position:absolute;left:0;top:336px;width:1200px;text-align:center;font-size:14px}
.footer .copy b{color:var(--gold);font-weight:400}
</style>
</head>
<body>

<div class="topbar">
  <div class="social"><span></span><span></span><span></span></div>
  <div class="contact">
    <span><svg width="12" height="12" viewBox="0 0 24 24"><path d="M6.6 10.8a15 15 0 0 0 6.6 6.6l2.2-2.2c.3-.3.7-.4 1-.2 1.1.4 2.3.6 3.6.6.6 0 1 .4 1 1V20c0 .6-.4 1-1 1A17 17 0 0 1 3 4c0-.6.4-1 1-1h3.5c.6 0 1 .4 1 1 0 1.3.2 2.5.6 3.6.1.3 0 .7-.2 1z" fill="#d3a33a"/></svg>01 234 567 890</span>
    <span><svg width="13" height="11" viewBox="0 0 24 18"><rect x="1" y="1" width="22" height="16" fill="none" stroke="#d3a33a" stroke-width="2"/><path d="M1 1l11 9 11-9" fill="none" stroke="#d3a33a" stroke-width="2"/></svg>info@corvenahotel.com</span>
  </div>
</div>

<header class="header">
  <div class="brand"><span class="mark"></span>Corvena Hotel</div>
  <nav class="nav"><span>HOME</span><span>ABOUT</span><span>ROOMS</span><span>NEWS</span><span>CONTACT</span></nav>
  <div class="btn">Book Now <span class="dot"></span></div>
</header>

<section class="hero" role="img" aria-label="Hotel bedroom with white bedding and lamp">
  <div class="abs eyebrow">LUXURY HOTEL &amp; BEST RESORT</div>
  <h1 class="abs serif">ENJOY A LUXURY<br>EXPERIENCE</h1>
  <div class="abs slides"><span>01</span><span class="rule"></span><span style="position:absolute;top:140px;left:-6px">04</span></div>
  <div class="booking">
    <label style="left:124px">CHECK-IN</label>
    <label style="left:368px">CHECK-OUT</label>
    <label style="left:607px">GUESTS</label>
    <div class="field" style="left:124px;width:223px"><span>-- / -- / --</span><span>▦</span></div>
    <div class="field" style="left:368px;width:219px"><span>-- / -- / --</span><span>▦</span></div>
    <div class="field" style="left:607px;width:228px"><span>00</span><span>⌄</span></div>
    <div class="btn">Check Availability <span class="dot"></span></div>
  </div>
</section>

<section class="welcome">
  <div class="abs emblem" role="img" aria-label="Hotel emblem artwork"></div>
  <div class="abs eyebrow">WELCOME TO</div>
  <h2 class="abs serif">CORVENA HOTEL</h2>
  <p class="abs">Lorem ipsum dolor sit amet, consec adiscing elit. Sed quis faucibus eros. Ut molestie odio est, et ultrices libero tempus eget. Mauris egestas conectetur nisl, sed tempus massa porttitor et. Integer s</p>
  <div class="btn">Learn More <span class="dot"></span></div>
</section>

<section class="promotions">
  <div class="abs section-eyebrow" style="left:0;top:1103px">BEST MONTHLY</div>
  <h2 class="abs section-title serif" style="left:0;top:1126px;font-size:66px">PROMOTIONS</h2>

  <div class="room" style="left:100px;top:1224px;width:316px;height:248px">
    <div class="photo" role="img" aria-label="Double bed room with sofa and artwork" style="background:linear-gradient(135deg,#c79a52,#e8d6b4 50%,#8a6a44)"></div>
    <div class="name">Double Bed Room</div>
    <div class="meta"><span><svg width="12" height="12" viewBox="0 0 24 24" fill="none" stroke="#fff" stroke-width="2"><circle cx="12" cy="8" r="4"/><path d="M4 22c0-5 4-8 8-8s8 3 8 8"/></svg>2 Guests</span><span><svg width="12" height="12" viewBox="0 0 24 24" fill="none" stroke="#fff" stroke-width="2"><rect x="3" y="3" width="18" height="18"/><path d="M8 16l8-8"/></svg>23 FT</span></div>
  </div>
  <div class="room" style="left:441px;top:1224px;width:318px;height:521px">
    <div class="photo" role="img" aria-label="Double bed room with wooden wall panels" style="background:linear-gradient(180deg,#b89a7a,#d8c3a8 55%,#8f8478)"></div>
    <div class="name">Double Bed Room</div>
    <div class="meta"><span><svg width="12" height="12" viewBox="0 0 24 24" fill="none" stroke="#fff" stroke-width="2"><circle cx="12" cy="8" r="4"/><path d="M4 22c0-5 4-8 8-8s8 3 8 8"/></svg>1 Guests</span><span><svg width="12" height="12" viewBox="0 0 24 24" fill="none" stroke="#fff" stroke-width="2"><rect x="3" y="3" width="18" height="18"/><path d="M8 16l8-8"/></svg>18 FT</span></div>
  </div>
  <div class="room" style="left:784px;top:1224px;width:318px;height:248px">
    <div class="photo" role="img" aria-label="Family room with grey upholstered bed" style="background:linear-gradient(135deg,#cfcac3,#e9e6e1 50%,#9c948a)"></div>
    <div class="name">Family Room</div>
    <div class="meta"><span><svg width="12" height="12" viewBox="0 0 24 24" fill="none" stroke="#fff" stroke-width="2"><circle cx="12" cy="8" r="4"/><path d="M4 22c0-5 4-8 8-8s8 3 8 8"/></svg>4 Guests</span><span><svg width="12" height="12" viewBox="0 0 24 24" fill="none" stroke="#fff" stroke-width="2"><rect x="3" y="3" width="18" height="18"/><path d="M8 16l8-8"/></svg>23 FT</span></div>
  </div>
  <div class="room" style="left:100px;top:1497px;width:316px;height:248px">
    <div class="photo" role="img" aria-label="Single bed room with white walls" style="background:linear-gradient(135deg,#dedad3,#f1eee9 50%,#8e877e)"></div>
    <div class="name">Single Bed Room</div>
    <div class="meta"><span><svg width="12" height="12" viewBox="0 0 24 24" fill="none" stroke="#fff" stroke-width="2"><circle cx="12" cy="8" r="4"/><path d="M4 22c0-5 4-8 8-8s8 3 8 8"/></svg>1 Guests</span><span><svg width="12" height="12" viewBox="0 0 24 24" fill="none" stroke="#fff" stroke-width="2"><rect x="3" y="3" width="18" height="18"/><path d="M8 16l8-8"/></svg>18 FT</span></div>
  </div>
  <div class="room" style="left:784px;top:1497px;width:318px;height:248px">
    <div class="photo" role="img" aria-label="Modern hotel exterior with blue sky" style="background:linear-gradient(135deg,#5d8fc4,#c9d7e4 45%,#9a7a66)"></div>
    <div class="name">Single Room</div>
    <div class="meta"><span><svg width="12" height="12" viewBox="0 0 24 24" fill="none" stroke="#fff" stroke-width="2"><circle cx="12" cy="8" r="4"/><path d="M4 22c0-5 4-8 8-8s8 3 8 8"/></svg>1 Guests</span><span><svg width="12" height="12" viewBox="0 0 24 24" fill="none" stroke="#fff" stroke-width="2"><rect x="3" y="3" width="18" height="18"/><path d="M8 16l8-8"/></svg>18 FT</span></div>
  </div>
</section>

<section class="amenities" role="img" aria-label="Dark green band over a blurred lobby background">
  <div class="amenity" style="left:98px">
    <svg width="52" height="52" viewBox="0 0 52 52" fill="none" stroke="#d3a33a" stroke-width="2"><circle cx="20" cy="18" r="12"/><circle cx="20" cy="14" r="3"/><path d="M27 27l18 18M38 38l-5 5M43 43l-4 4"/></svg>
    <div><div class="t">Smart Key</div><div class="s">Lorem ipsum dolor</div></div>
  </div>
  <div class="amenity" style="left:362px">
    <svg width="52" height="52" viewBox="0 0 52 52" fill="none" stroke="#d3a33a" stroke-width="2"><path d="M26 6a10 10 0 0 1 10 10c0 8-10 18-10 18S16 24 16 16A10 10 0 0 1 26 6z"/><circle cx="26" cy="16" r="3.5"/><path d="M12 30l-8 14h44l-8-14"/></svg>
    <div><div class="t">GPS</div><div class="s">Driving Location</div></div>
  </div>
  <div class="amenity" style="left:602px">
    <svg width="52" height="52" viewBox="0 0 52 52" fill="none" stroke="#d3a33a" stroke-width="2"><circle cx="20" cy="18" r="12"/><circle cx="20" cy="14" r="3"/><path d="M27 27l18 18M38 38l-5 5M43 43l-4 4"/></svg>
    <div><div class="t">Room Service</div><div class="s">Lorem ipsum dolor</div></div>
  </div>
  <div class="amenity" style="left:870px">
    <svg width="52" height="52" viewBox="0 0 52 52" fill="none" stroke="#d3a33a" stroke-width="2"><path d="M26 6a10 10 0 0 1 10 10c0 8-10 18-10 18S16 24 16 16A10 10 0 0 1 26 6z"/><circle cx="26" cy="16" r="3.5"/><path d="M12 30l-8 14h44l-8-14"/></svg>
    <div><div class="t">Store Luggage</div><div class="s">Driving Location</div></div>
  </div>
</section>

<section class="services">
  <div class="abs eyebrow">HOTEL SERVICES</div>
  <h2 class="abs serif">Check all Rooms<br>&amp; Best Suites</h2>
  <p class="abs">Lorem ipsum dolor sit amet, consec adiscing elit. Sed quis faucibus eros. Ut molestie odio est, et ultrices libero tempus eget. Mauris egestas conectetur nisl, sed tempus massa porttitor et. Integer semleo felis, nec consequat dui cursus nec.</p>
  <div class="abs" role="img" aria-label="Traveller with a red suitcase by the sea" style="left:549px;top:2174px;width:365px;height:371px;background:linear-gradient(180deg,#c9dcea 0%,#8fb3c8 45%,#6e8a6a 70%,#b9ad9c 100%)"></div>
  <div class="thumb" role="img" aria-label="Double room" style="top:2209px;background:linear-gradient(135deg,#8d857c,#e6e1da)"></div>
  <div class="thumb" role="img" aria-label="Small suite" style="top:2316px;background:linear-gradient(135deg,#c7b59b,#f0ebe3)"></div>
  <div class="thumb" role="img" aria-label="Family room" style="top:2422px;background:linear-gradient(135deg,#57504a,#d9d3cb)"></div>
  <div class="lbl" style="top:2229px"><small>All Excluseive</small><b>Double Room</b></div>
  <div class="lbl" style="top:2336px"><small>Breakfast</small><b>Small Suite</b></div>
  <div class="lbl" style="top:2442px"><small>Drinks Included</small><b>Family Room</b></div>
</section>

<section class="testimonial">
  <div class="photo" role="img" aria-label="Folded white towels with a frangipani flower"></div>
  <div class="panel"></div>
  <div class="abs eyebrow">Testimonial</div>
  <h2 class="abs serif">What Client Say</h2>
  <blockquote>Nullam a turpis eu est posuere aliquet nec nec nisl. Nam ac lectus semr, eleifend felis ultrices, condimentum metus. Donec ut dui dictum, luctus justo in, luctus libero.</blockquote>
  <div class="abs stars">
    <svg width="86" height="16" viewBox="0 0 86 16"><g fill="#d3a33a"><path id="st" d="M8 0l2.4 5 5.6.6-4.2 3.8 1.2 5.6L8 12.2 3 15l1.2-5.6L0 5.6 5.6 5z"/><use href="#st" x="17.5"/><use href="#st" x="35"/><use href="#st" x="52.5"/><use href="#st" x="70"/></g></svg>
  </div>
  <div class="abs who">Jhon Doe</div>
  <div class="abs arrows">
    <span style="background:#d8d8d8"><svg width="14" height="14" viewBox="0 0 14 14"><path d="M9 2L4 7l5 5" fill="none" stroke="#555" stroke-width="2.4"/></svg></span>
    <span style="background:#fff"><svg width="14" height="14" viewBox="0 0 14 14"><path d="M5 2l5 5-5 5" fill="none" stroke="#222" stroke-width="2.4"/></svg></span>
  </div>
</section>

<section class="gallery">
  <h2 class="abs section-title serif" style="left:0;top:3232px;font-size:60px">Gallery</h2>
  <div class="tile" role="img" aria-label="Dark modern bedroom" style="left:100px;top:3320px;width:248px;height:357px;background:linear-gradient(160deg,#3a342e,#8b7457 55%,#cbbfae)"></div>
  <div class="tile" role="img" aria-label="Dining area with round table" style="left:348px;top:3320px;width:252px;height:179px;background:linear-gradient(135deg,#6b5a48,#d7cbbb)"></div>
  <div class="tile" role="img" aria-label="Bright bedroom with city view" style="left:348px;top:3499px;width:252px;height:178px;background:linear-gradient(135deg,#a9c3db,#f0eee9 60%,#c9c2b8)"></div>
  <div class="tile" role="img" aria-label="Guest with suitcase in hotel corridor" style="left:600px;top:3320px;width:250px;height:357px;background:linear-gradient(180deg,#c89a5a,#e9d3a9 50%,#7c6047)"></div>
  <div class="tile" role="img" aria-label="Housekeeper making a bed" style="left:850px;top:3320px;width:252px;height:179px;background:linear-gradient(135deg,#8c8a86,#f1f0ed)"></div>
  <div class="tile" role="img" aria-label="Guest relaxing by the pool" style="left:850px;top:3499px;width:252px;height:178px;background:linear-gradient(180deg,#cfe0ea,#6fb7cf 60%,#3d8aa8)"></div>
</section>

<section class="contact-sec" role="img" aria-label="Breakfast tray on a bed with juice and pastries"></section>
<div class="contact-card">
  <h2 class="serif">Get In Touch</h2>
  <div class="input" style="top:132px;height:42px">Name</div>
  <div class="input" style="top:181px;height:44px">Email</div>
  <div class="input" style="top:236px;height:44px">Phone</div>
  <div class="input" style="top:289px;height:84px">Your Message</div>
  <div class="btn">Submit Now <span class="dot"></span></div>
</div>

<footer class="footer">
  <div class="brand"><span class="mark"></span>Corvena Hotel</div>
  <div class="social"><span></span><span></span><span></span></div>

  <h4 style="left:420px">Quick Links</h4>
  <ul style="left:420px;top:102px"><li>Home</li><li>About</li><li>Rooms</li><li>News</li><li>Contact</li></ul>

  <h4 style="left:589px">Contact Info</h4>
  <div class="info">
    <div><svg width="12" height="16" viewBox="0 0 12 16"><path d="M6 0a6 6 0 0 1 6 6c0 4.5-6 10-6 10S0 10.5 0 6a6 6 0 0 1 6-6z" fill="#d3a33a"/><circle cx="6" cy="6" r="2" fill="#2b2b2b"/></svg><span>24 Harbour Street,<br>Old Quay District</span></div>
    <div><svg width="13" height="13" viewBox="0 0 24 24"><path d="M6.6 10.8a15 15 0 0 0 6.6 6.6l2.2-2.2c.3-.3.7-.4 1-.2 1.1.4 2.3.6 3.6.6.6 0 1 .4 1 1V20c0 .6-.4 1-1 1A17 17 0 0 1 3 4c0-.6.4-1 1-1h3.5c.6 0 1 .4 1 1 0 1.3.2 2.5.6 3.6.1.3 0 .7-.2 1z" fill="#d3a33a"/></svg><span>01 234 567 890</span></div>
    <div><svg width="13" height="11" viewBox="0 0 24 18"><rect x="0" y="0" width="24" height="18" fill="#d3a33a"/><path d="M1 1l11 9 11-9" fill="none" stroke="#2b2b2b" stroke-width="2"/></svg><span>info@corvenahotel.com</span></div>
  </div>

  <h4 style="left:832px">Newsletter</h4>
  <div class="nl">
    <div>Sed quis faucibus eros. Ut molestie odio est, et ultrices libero tempus eget.</div>
    <div class="email"><span>Enter email address</span><svg width="16" height="16" viewBox="0 0 16 16"><path d="M15 1L1 7l5 2 2 6z" fill="#d3a33a"/></svg></div>
  </div>

  <div class="rule"></div>
  <div class="copy">© 2022 <b>Corvena Hotel</b>. All right reserved</div>
</footer>

</body>
</html>
```